Business Card Design

We like to use greens as you will see in our logo (but not TOO much green). We are a Dental Clinic in a somewhat eccentric community. We do not like the dated sharp designs which we see many dentists use. We're looking for something bright and fresh while still maintaining the integrity of the profession. Elegance is not necessarily what we are going for... we need for the design to be "mature" but also up-lifting.

See our logo.
Updates

Project Deadline Extended
Reason: We have 5 designs which we like. But we'd like to see a few more before committing to a design.

Project Deadline Extended
Reason: We are awaiting revisions to this project. We are still welcoming designs while we wait to see if designers are able to provide to us the revisions we require in order to proceed with a selection.

Target Market(s)

Younger families - ages late 20's to early 40's

Industry/Entity Type

Business

Contact Information for Business Card

Corwel T. Banfry DDS 2730 W. Halvert Rd. Ste. 7 Royal Oak, MI 48391 (248)555-0174 FX (248)555-0189 info@BrightwellDentalCareMi.com BrigthwellDentalCareMi.com on the back of the card we need an appointment reminder (For____ Date___ Time____) with "If you are unable to keep your appointment, kindly give 48 hours notice" at the bottom. No use of teeth in the design. DOUBLE SIDED DESIGN

Requirements
Should not have
• The use of pictures of teeth

```html
<!DOCTYPE html>
<html lang="en">
<head>
<meta charset="utf-8">
<title>Brightwell Dental Care – Business Card</title>
<link rel="stylesheet" href="https://fonts.googleapis.com/css2?family=Open+Sans:ital,wght@0,400;0,600;0,700;1,400&family=Cinzel:wght@500&display=swap">
<style>
  :root {
    --backdrop: #efece6;
    --card: #ffffff;
    --card-edge: #3a3a3a;
    --green-dark: #1f6b35;
    --green-mid: #7fbf5a;
    --green-soft: #b9dca0;
    --ink: #2b2b2b;
    --rule: #555555;
  }
  * { margin: 0; padding: 0; box-sizing: border-box; }
  html, body { width: 1200px; height: 1184px; overflow: hidden; }
  body {
    background: var(--backdrop);
    font-family: "Open Sans", Arial, sans-serif;
    color: var(--ink);
    position: relative;
  }
  .card {
    position: absolute;
    background: var(--card);
    border: 2px solid var(--card-edge);
    overflow: hidden;
  }
  .card--front { left: 239px; top: 29px; width: 936px; height: 538px; }
  .card--back  { left: 29px; top: 596px; width: 943px; height: 537px; }

  .accent-circle {
    position: absolute;
    border-radius: 50%;
    background: var(--green-soft);
    opacity: 0.55;
  }
  .card--front .accent-circle { left: 600px; top: 150px; width: 330px; height: 330px; }
  .card--back .accent-circle { left: 322px; top: 55px; width: 300px; height: 300px; opacity: 0.45; }

  /* Front */
  .brand { position: absolute; left: 49px; top: 78px; color: var(--green-dark); font-weight: 600; }
  .brand__name { font-size: 84px; line-height: 1; letter-spacing: -1px; display: flex; align-items: center; gap: 16px; }
  .brand__dot { width: 30px; height: 30px; border-radius: 50%; background: var(--green-dark); display: inline-block; }
  .brand__sub { font-size: 44px; line-height: 1; margin-top: 14px; letter-spacing: 1px; }

  .contact { position: absolute; left: 52px; top: 280px; list-style: none; font-size: 23px; }
  .contact li { display: flex; align-items: center; gap: 8px; height: 41px; }
  .contact svg { width: 18px; height: 18px; flex: none; }

  .address { position: absolute; left: 52px; top: 448px; font-size: 23px; line-height: 33px; font-style: normal; }

  .dentist { position: absolute; left: 600px; top: 355px; width: 330px; text-align: center; }
  .dentist__name { font-size: 32px; font-weight: 700; color: var(--green-dark); line-height: 1.2; }
  .dentist__title { font-size: 24px; line-height: 1.4; }

  /* Back */
  .appt-title {
    position: absolute; left: 0; right: 0; top: 88px; text-align: center;
    font-family: "Cinzel", Georgia, serif; font-weight: 500; font-size: 38px;
    color: var(--green-dark); letter-spacing: 1px;
  }
  .field { position: absolute; font-size: 25px; display: flex; align-items: baseline; }
  .field__line { border-bottom: 2px dotted var(--rule); margin-left: 14px; height: 1px; }
  .field--name { left: 55px; top: 160px; }
  .field--name .field__line { width: 690px; }
  .field--date { left: 55px; top: 227px; }
  .field--date .field__line { width: 246px; margin-left: 50px; }
  .field--time { left: 423px; top: 227px; }
  .field--time .field__line { width: 246px; }
  .field__unit { margin-left: 12px; }

  .next { position: absolute; left: 55px; top: 290px; font-size: 25px; display: flex; align-items: center; }
  .next__box { width: 170px; height: 37px; border: 2px solid var(--rule); border-radius: 4px; margin-left: 14px; }
  .next__box:first-of-type { margin-left: 29px; }

  .days { position: absolute; left: 55px; top: 380px; display: flex; align-items: center; font-weight: 700; font-size: 26px; }
  .days span { margin-right: 12px; }
  .days i { width: 58px; height: 36px; border: 2px solid var(--rule); border-radius: 4px; margin-right: 16px; }

  .notice { position: absolute; left: 0; right: 0; top: 462px; text-align: center; font-style: italic; font-size: 24px; }
</style>
</head>
<body>
  <section class="card card--front" aria-label="Business card front">
    <div class="accent-circle" aria-hidden="true"></div>
    <div class="brand">
      <div class="brand__name">Brightwell <span class="brand__dot"></span></div>
      <div class="brand__sub">DENTAL CARE</div>
    </div>
    <ul class="contact">
      <li><svg viewBox="0 0 20 20"><path fill="#1f6b35" d="M5 2l3 4-2 2c1 3 3 5 6 6l2-2 4 3-2 3C9 18 2 11 2 4z"/></svg>(248)555-0174</li>
      <li><svg viewBox="0 0 20 20"><rect x="4" y="2" width="12" height="6" fill="#1f6b35"/><rect x="2" y="8" width="16" height="8" rx="2" fill="#1f6b35"/><rect x="5" y="11" width="10" height="2" fill="#fff"/></svg>(248)555-0189</li>
      <li><svg viewBox="0 0 20 20"><rect x="1" y="4" width="18" height="12" rx="2" fill="#1f6b35"/><path d="M2 5l8 6 8-6" stroke="#fff" stroke-width="1.6" fill="none"/></svg>info@BrightwellDentalCareMi.com</li>
      <li><svg viewBox="0 0 20 20"><circle cx="10" cy="10" r="8" fill="none" stroke="#1f6b35" stroke-width="2"/><ellipse cx="10" cy="10" rx="3.5" ry="8" fill="none" stroke="#1f6b35" stroke-width="1.5"/><path d="M2 10h16" stroke="#1f6b35" stroke-width="1.5"/></svg>BrigthwellDentalCareMi.com</li>
    </ul>
    <address class="address">2730 W. Halvert Rd.<br>Ste. 7 Royal Oak, MI 48391</address>
    <div class="dentist">
      <div class="dentist__name">Corwel T. Banfry</div>
      <div class="dentist__title">DDS</div>
    </div>
  </section>

  <section class="card card--back" aria-label="Business card back, appointment reminder">
    <div class="accent-circle" aria-hidden="true"></div>
    <h2 class="appt-title">YOUR APPOINTMENT</h2>
    <div class="field field--name">Name :<span class="field__line"></span></div>
    <div class="field field--date">Date :<span class="field__line"></span></div>
    <div class="field field--time">Time :<span class="field__line"></span><span class="field__unit">am / pm</span></div>
    <div class="next">Next Appointment<span class="next__box"></span><span class="next__box"></span><span class="next__box"></span></div>
    <div class="days">
      <span>MON</span><i></i><span>TUE</span><i></i><span>WED</span><i></i><span>THU</span><i></i><span>FRI</span><i></i><span>SAT</span><i></i>
    </div>
    <p class="notice">If you are unable to keep your appointment, kindly give 48 hours notice</p>
  </section>
</body>
</html>
```